KRV Boltmaster Manufacturer New Web Design

We need a new theme designed for metal fastener manufacturing company, KRV Boltmaster Group, a $60M division of Marrowfield Forge Holdings, Inc. We manufacture screw, pins and washers to industrial customers (non-Automotive) such as HN Homeware, Paul Brenner, LUX, Venmora, etc. Our current website is www.boltmaster.example. We would like to stick with the same logo/color scheme, however, I'm aiming to modernize the website's look and feel.

Here are some of our competitor's websites:
- https://www.torvalink.example/
- http://glenrivet.example/
- http://www.harlowbuiltjoining.example/
- http://lugsandcustoms.example/
- http://www.dunmerebolt.example/

Target Market(s)

We primarily want to target engineers working in the following markets:
- Appliance (HN Homeware, Frostavel)
- Ag (Brenner, LUX)
- Recreational Vehicle (Venmora, Tundra Fox)
- Outdoor Power (Brellvik, Pask)

We secondarily want to target buyers working at the above markets as well as buyers at Fastener distributors such as Boltique, Parts Dynamics, Kessel Fordham.

Industry/Entity Type

Metal Forging

Number of Pages Required

1 page

Requirements
Must have
• For products: "Threaded" product as the primary focus. "Pins" product is the secondary focus, followed by all others.
• Please use same logo and color scheme as I do not plan to change.
Nice to have
• Highlight our featured proprietary products (pamphlets attached). KRV Boltmaster's GRIP-N, KelDrive, Boltmaster Coil, Avalanche.

```html
<!DOCTYPE html>
<html lang="en">
<head>
<meta charset="utf-8">
<title>KRV Boltmaster Group</title>
<link href="https://fonts.googleapis.com/css2?family=Roboto:wght@400;500;700&display=swap" rel="stylesheet">
<style>
:root{
  --navy:#23264a;
  --navy-deep:#1f2244;
  --teal:#22c9a0;
  --sky:#5aaed6;
  --brand:#1a9fd6;
  --ink:#2b2b2b;
  --muted:#6b6b6b;
  --grey-bg:#f1f1f1;
  --white:#fff;
}
*{box-sizing:border-box;margin:0;padding:0}
html,body{width:1200px;height:2423px;overflow:hidden}
body{font-family:"Roboto",sans-serif;color:var(--ink);background:var(--white);position:relative}
.wrap{position:absolute;left:200px;width:800px}

/* header */
.site-header{position:absolute;top:0;left:0;width:1200px;height:94px;background:var(--white)}
.brand{position:absolute;left:200px;top:14px;display:flex;align-items:center;gap:8px}
.brand-mark{width:38px;height:38px;border-radius:50%;background:var(--brand);flex:none}
.brand-name{font-size:21px;font-weight:500;color:var(--brand);white-space:nowrap}
.contact-chip{position:absolute;top:20px;display:flex;gap:10px;align-items:center;font-size:12px;color:var(--ink)}
.contact-chip .ico{width:30px;height:30px;border:1px solid #ddd;border-radius:3px;display:flex;align-items:center;justify-content:center}
.contact-chip small{display:block;color:#999;font-size:12px}
.main-nav{position:absolute;left:200px;top:73px;width:800px;height:42px;background:var(--navy);z-index:3;display:flex;align-items:center}
.main-nav ul{display:flex;list-style:none;padding-left:20px;gap:22px;font-size:12px;color:var(--white)}
.nav-search{position:absolute;left:595px;top:13px}
.quote-btn{position:absolute;right:0;top:0;width:144px;height:42px;background:var(--sky);color:var(--white);font-size:12px;font-weight:700;display:flex;align-items:center;justify-content:center}

/* hero */
.hero{position:absolute;top:94px;left:0;width:1200px;height:508px;background:linear-gradient(100deg,#3d4d58 0%,#5b6a70 35%,#4a4440 65%,#2f2c2e 100%)}
.hero h1{position:absolute;left:199px;top:155px;font-size:38px;font-weight:500;color:var(--white)}
.hero p{position:absolute;left:199px;top:212px;width:420px;font-size:13.5px;line-height:20px;color:var(--white)}
.btn{position:absolute;height:48px;display:flex;align-items:center;justify-content:center;color:var(--white);font-size:13px;font-weight:700}
.btn-teal{left:199px;top:298px;width:141px;background:var(--teal)}
.btn-sky{left:352px;top:298px;width:139px;background:var(--sky)}
.hero-arrow{position:absolute;top:238px;width:40px;height:40px;border:2px solid var(--white);border-radius:50%}
.dots{position:absolute;left:589px;top:440px;display:flex;gap:4px}
.dots i{width:8px;height:8px;border-radius:50%;background:#ccc;display:block}
.dots i.on{background:var(--teal)}

/* section headings */
.sec-title{font-size:24px;font-weight:500;color:var(--ink)}
.sec-title::after{content:"";display:block;width:40px;height:3px;background:var(--sky);margin-top:10px}

/* products */
.products{top:662px}
.product-row{display:flex;margin-top:42px}
.product{width:207px;text-align:center}
.product-icon{width:64px;height:64px;margin:0 auto;border:1px dashed #aaa;border-radius:50%;display:flex;align-items:center;justify-content:center}
.product h3{font-size:13px;font-weight:500;margin-top:18px}
.product p{font-size:11.5px;color:var(--muted);line-height:18px;margin-top:10px}

/* featured */
.featured-band{position:absolute;top:942px;left:0;width:1200px;height:520px;background:var(--grey-bg)}
.featured{top:1008px}
.cards{display:flex;gap:11px;margin-top:42px}
.card{width:192px;height:299px;background:var(--white);position:relative}
.card-img{height:133px}
.card h4{font-size:11px;font-weight:500;padding:15px 10px 10px;border-bottom:1px solid #e6e6e6;white-space:nowrap}
.card .lead{font-size:11.5px;line-height:15px;color:var(--muted);padding:8px 10px 0;height:44px}
.card h5{font-size:12px;font-weight:500;padding:4px 10px 2px}
.card ul{list-style:none;font-size:11.5px;color:var(--muted);padding:0 10px;line-height:17px}
.read-btn{position:absolute;left:13px;bottom:0;width:70px;height:22px;background:var(--sky);color:var(--white);font-size:10px;display:flex;align-items:center;justify-content:center}

/* news */
.news{top:1522px}
.news-row{display:flex;gap:44px;margin-top:38px}
.news-item{width:378px}
.news-img{height:176px}
.news-body{display:flex;margin-top:24px}
.news-date{width:52px;text-align:center;font-size:18px;font-weight:700;line-height:20px}
.news-date span{display:block;font-size:11px;font-weight:500}
.news-text{border-left:1px solid #ccc;padding-left:18px;width:300px}
.news-text h4{font-size:12.5px;font-weight:700;line-height:16px}
.news-text p{font-size:11.5px;color:var(--muted);line-height:16px;margin-top:6px}
.news-text a{display:block;font-size:11.5px;color:var(--sky);margin-top:12px;text-decoration:none}

/* cta */
.cta{position:absolute;top:1978px;left:0;width:1200px;height:100px;background:var(--teal)}
.cta p{position:absolute;left:200px;top:26px;width:620px;font-size:15px;font-weight:500;line-height:24px;color:var(--white)}
.cta-btn{position:absolute;left:864px;top:30px;width:136px;height:43px;background:var(--white);color:var(--teal);font-size:13px;font-weight:700;display:flex;align-items:center;justify-content:center}

/* footer */
.site-footer{position:absolute;top:2078px;left:0;width:1200px;height:345px;background:var(--navy)}
.foot-brand{position:absolute;left:200px;top:62px;display:flex;align-items:center;gap:8px;width:260px}
.foot-brand .brand-mark{width:34px;height:34px}
.foot-brand .brand-name{font-size:18px}
.foot-about{position:absolute;left:200px;top:134px;width:250px;font-size:11.5px;line-height:20px;color:var(--white)}
.socials{position:absolute;left:200px;top:212px;display:flex;gap:18px}
.socials i{width:12px;height:12px;border-radius:50%;background:var(--white);display:block}
.foot-col{position:absolute;top:70px;color:var(--white)}
.foot-col h6{font-size:12.5px;font-weight:700}
.foot-col h6::after{content:"";display:block;width:40px;height:2px;background:var(--sky);margin-top:8px}
.info-links{display:grid;grid-template-columns:120px 160px;font-size:11.5px;line-height:24px;margin-top:30px;list-style:none}
.touch{list-style:none;margin-top:30px;font-size:11.5px;line-height:18px}
.touch li{display:flex;gap:14px;margin-bottom:14px}
.copyright{position:absolute;left:0;top:283px;width:1200px;height:62px;border-top:1px solid #3a3d5e;background:var(--navy-deep);color:var(--white);font-size:11.5px;display:flex;align-items:center;justify-content:center}
</style>
</head>
<body>

<header class="site-header">
  <div class="brand"><span class="brand-mark"></span><span class="brand-name">KRV Boltmaster Group</span></div>
  <div class="contact-chip" style="left:664px">
    <span class="ico"><svg width="14" height="10" viewBox="0 0 14 10"><rect x="0.5" y="0.5" width="13" height="9" fill="none" stroke="#999"/><path d="M0.5 0.5 7 6 13.5 0.5" fill="none" stroke="#999"/></svg></span>
    <div>E-mail :<small>sales@boltmaster.example</small></div>
  </div>
  <div class="contact-chip" style="left:882px">
    <span class="ico"><svg width="12" height="12" viewBox="0 0 24 24"><path d="M6.6 10.8a15 15 0 0 0 6.6 6.6l2.2-2.2a1 1 0 0 1 1-.25 11.4 11.4 0 0 0 3.6.6 1 1 0 0 1 1 1V20a1 1 0 0 1-1 1A17 17 0 0 1 3 4a1 1 0 0 1 1-1h3.5a1 1 0 0 1 1 1c0 1.25.2 2.45.6 3.6a1 1 0 0 1-.25 1z" fill="#999"/></svg></span>
    <div>Call Us :<small>555-014-2290</small></div>
  </div>
</header>

<nav class="main-nav">
  <ul><li>Home</li><li>Products</li><li>Capabilities</li><li>Engineering</li><li>Quality</li><li>About Us</li><li>Contact/Quote Request</li></ul>
  <svg class="nav-search" width="16" height="16" viewBox="0 0 16 16"><circle cx="6.5" cy="6.5" r="5" fill="none" stroke="#fff" stroke-width="2"/><path d="M10 10l5 5" stroke="#fff" stroke-width="2"/></svg>
  <div class="quote-btn">GET A QUOTE</div>
</nav>

<section class="hero" role="img" aria-label="Factory worker operating machinery on a fastener production floor">
  <h1>Better fasteners for Better Products</h1>
  <p>KRV Boltmaster Group is a leading designer and manufacturer of value added, high quality engineered hardware solutions.</p>
  <div class="btn btn-teal">READ MORE</div>
  <div class="btn btn-sky">CONTACT US</div>
  <svg class="hero-arrow" style="left:77px" viewBox="0 0 40 40"><path d="M23 12l-8 8 8 8" fill="none" stroke="#fff" stroke-width="2"/></svg>
  <svg class="hero-arrow" style="left:1079px" viewBox="0 0 40 40"><path d="M17 12l8 8-8 8" fill="none" stroke="#fff" stroke-width="2"/></svg>
  <div class="dots"><i></i><i></i><i class="on"></i></div>
</section>

<section class="wrap products">
  <h2 class="sec-title">Our Products</h2>
  <div class="product-row">
    <div class="product">
      <div class="product-icon"><svg width="34" height="30" viewBox="0 0 34 30"><rect x="4" y="8" width="24" height="14" fill="none" stroke="#22c9a0" stroke-width="2"/><path d="M9 8v14M14 8v14M19 8v14M24 8v14" stroke="#22c9a0"/></svg></div>
      <h3>THREADED</h3><p>KRV Boltmaster Group has devel-<br>oped multiple screw..</p>
    </div>
    <div class="product">
      <div class="product-icon"><svg width="32" height="32" viewBox="0 0 32 32"><path d="M6 27L21 12" stroke="#22c9a0" stroke-width="2.5"/><circle cx="24" cy="9" r="4.5" fill="none" stroke="#22c9a0" stroke-width="2"/></svg></div>
      <h3>PINS</h3><p>Our Pin business is the traditional<br>Harlan Pike product line..</p>
    </div>
    <div class="product">
      <div class="product-icon"><svg width="30" height="32" viewBox="0 0 30 32"><circle cx="15" cy="9" r="6" fill="#22c9a0"/><rect x="12" y="14" width="6" height="8" fill="#22c9a0"/><rect x="5" y="22" width="20" height="5" fill="#22c9a0"/></svg></div>
      <h3>STAMPINGS</h3><p>KRV Boltmaster Group is the<br>largest, most diverse..</p>
    </div>
    <div class="product">
      <div class="product-icon"><svg width="30" height="32" viewBox="0 0 30 32"><path d="M12 27A11 11 0 1 1 18 27" fill="none" stroke="#22c9a0" stroke-width="3.5"/></svg></div>
      <h3>LOCK WASHERS</h3><p>Historically, KRV Boltmaster<br>Group's Helical Spring Lock</p>
    </div>
  </div>
</section>

<div class="featured-band"></div>
<section class="wrap featured">
  <h2 class="sec-title">Featured Proprietary Product</h2>
  <div class="cards">
    <article class="card">
      <div class="card-img" role="img" aria-label="Rows of threaded rolling screws" style="background:linear-gradient(135deg,#c9ccd0,#7d8288)"></div>
      <h4>GRIP-N THREAD-ROLLING SCREW</h4>
      <p class="lead">Trilobular screws typically require 40% more...</p>
      <h5>Features</h5><ul><li>→ Head styles</li><li>→ Point styles</li></ul>
      <div class="read-btn">Read More</div>
    </article>
    <article class="card">
      <div class="card-img" role="img" aria-label="Bolts and nuts on a wooden surface" style="background:linear-gradient(135deg,#8a6a55,#a9b4bc 55%,#5b4538)"></div>
      <h4>KELDRIVE</h4>
      <p class="lead">Dramatically advances fasten-ing performance</p>
      <h5>Features</h5><ul><li>→ Security</li><li>→ Engineered</li></ul>
      <div class="read-btn">Read More</div>
    </article>
    <article class="card">
      <div class="card-img" role="img" aria-label="Screwdriver driving a brass screw into wood" style="background:linear-gradient(135deg,#d8c6a8,#a8875c 60%,#6e5a3e)"></div>
      <h4>BOLTMASTER COIL</h4>
      <p class="lead">Controls loosening due to vibration, high heat...</p>
      <h5>Features</h5><ul><li>→ Anti-vibration</li><li>→ Engineered</li></ul>
      <div class="read-btn">Read More</div>
    </article>
    <article class="card">
      <div class="card-img" role="img" aria-label="Pile of blue zinc plated screws" style="background:linear-gradient(135deg,#6c9cc4,#3b6d98 55%,#88b4d6)"></div>
      <h4>AVALANCHE</h4>
      <p class="lead">Advances strip-out values and operating range</p>
      <h5>Features</h5><ul><li>→ Cost-savings</li><li>→ Efficiency</li></ul>
      <div class="read-btn">Read More</div>
    </article>
  </div>
</section>

<section class="wrap news">
  <h2 class="sec-title">News and Events</h2>
  <div class="news-row">
    <article class="news-item">
      <div class="news-img" role="img" aria-label="Blue plated bolts and nuts close-up" style="background:linear-gradient(135deg,#3f7fc0,#9cc6ea 50%,#2d5e96)"></div>
      <div class="news-body">
        <div class="news-date">25<span>Nov</span></div>
        <div class="news-text"><h4>MFH INTEGRATES LEADING MIDWEST FASTENER DIVISIONS</h4>
          <p>Effective immediately, Marrowfield Forge Holdings, a $16 billion diversified manufacturer of engineered products and specialty..</p>
          <a>Read More →</a></div>
      </div>
    </article>
    <article class="news-item">
      <div class="news-img" role="img" aria-label="Brass wood screws standing in soft focus" style="background:linear-gradient(135deg,#6b4a2c,#b98a55 50%,#4a3220)"></div>
      <div class="news-body">
        <div class="news-date">25<span>Nov</span></div>
        <div class="news-text"><h4>MFH INTEGRATES LEADING MIDWEST FASTENER DIVISIONS</h4>
          <p>Effective immediately, Marrowfield Forge Holdings, a $16 billion diversified manufacturer of engineered products and specialty..</p>
          <a>Read More →</a></div>
      </div>
    </article>
  </div>
</section>

<section class="cta">
  <p>KRV Boltmaster Group always strives to improve our customer's products through designing and manufacturing value-added, quality solutions</p>
  <div class="cta-btn">CONTACT US</div>
</section>

<footer class="site-footer">
  <div class="foot-brand"><span class="brand-mark"></span><span class="brand-name">KRV Boltmaster Group</span></div>
  <p class="foot-about">Known as KRV Boltmaster Group today, the company is the result of a 2010 merger of MFH businesses that have a long...</p>
  <div class="socials"><i></i><i></i><i></i><i></i></div>
  <div class="foot-col" style="left:483px">
    <h6>INFORMATION</h6>
    <ul class="info-links"><li>Home</li><li>Quality</li><li>Products</li><li>About Us</li><li>Capabilities</li><li>Contact/Quote Request</li><li>Engineering</li></ul>
  </div>
  <div class="foot-col" style="left:767px">
    <h6>GET IN TOUCH</h6>
    <ul class="touch">
      <li><svg width="14" height="14" viewBox="0 0 24 24"><path d="M6.6 10.8a15 15 0 0 0 6.6 6.6l2.2-2.2a1 1 0 0 1 1-.25 11.4 11.4 0 0 0 3.6.6 1 1 0 0 1 1 1V20a1 1 0 0 1-1 1A17 17 0 0 1 3 4a1 1 0 0 1 1-1h3.5a1 1 0 0 1 1 1c0 1.25.2 2.45.6 3.6a1 1 0 0 1-.25 1z" fill="#fff"/></svg><span>Phone : 555-014-2290</span></li>
      <li><svg width="14" height="16" viewBox="0 0 14 16"><path d="M7 0a6 6 0 0 1 6 6c0 4-6 10-6 10S1 10 1 6a6 6 0 0 1 6-6z" fill="#fff"/><circle cx="7" cy="6" r="2.2" fill="#23264a"/></svg><span>Address : 418 Anvil Row<br>Carden Falls, ST 00417</span></li>
      <li><svg width="14" height="10" viewBox="0 0 14 10"><rect width="14" height="10" fill="#fff"/><path d="M0 0 7 6 14 0" fill="none" stroke="#23264a"/></svg><span>E-mail : sales@boltmaster.example</span></li>
    </ul>
  </div>
  <div class="copyright">© Copyright 2017 boltmaster. All Rights Reserved.</div>
</footer>

</body>
</html>
```